Tide & Thistle Website Creation For Online Spirits Sales via MerrowVats.com

Want a Website developed that I will use to partner with Merrow Vats to sell my signature rum online. Merrow Vats will add the final code to make the website an e-commerce site. Website should have links to Social media pages, recipies, About, news and events, products. I have he domain name already just need a designer to make the website look professional. Need website capable of being viewed on iPhone and Android devices. Please use the color scheme that is on the label. The brand motto is: Celebrate Life With Family old and new friends. The bottle sent in the images will be replaced with and actual high resolution image of the bottle when it is produce on 27 DEC 21. Can give the selected designer access to develop the website. I have the hostbramble.com domain name. Final code will be added by a designer from MerrowVats.com to make it a e-commerce store.
Updates

I added more information to refine the design I wanted. I should have had this information available to the designers when I started the project.

Target Market(s)

Target Market is 25-50 year old who drink rum

Industry/Entity Type

Spirits. Using Website to sell Rum online

Number of Pages Required

1 page

Font styles to use
Sans Serif

Colors
00AB8E
00BBA5
67D7C9
C6EFE9
E9F9F6

Requirements
Must have
• Must look elegant and of high class. Rum is being market as a premium unnamed rum.
Nice to have
• Video of people drinking, smiling and celebrating

```html
<!DOCTYPE html>
<html lang="en">
<head>
<meta charset="utf-8">
<title>Tide &amp; Thistle — Premium Rum</title>
<link rel="stylesheet" href="https://fonts.googleapis.com/css2?family=Libre+Baskerville:wght@700&family=Roboto:ital,wght@0,400;0,500;0,700;1,400&display=swap">
<style>
:root{
  --green:#00ab8e;
  --green-2:#00bba5;
  --green-3:#67d7c9;
  --mint:#c6eff9;
  --ink:#111;
  --text:#555;
  --dark:#2b2b2b;
  --star:#f5b400;
  --line:#e2e2e2;
}
*{box-sizing:border-box;margin:0;padding:0}
html,body{width:1200px;height:3536px;overflow:hidden}
body{font-family:"Roboto",sans-serif;color:var(--text);background:#fff;position:relative}
.serif{font-family:"Libre Baskerville",serif;font-weight:700;text-transform:uppercase;color:var(--ink)}
a{color:inherit;text-decoration:none}

/* header */
.header{position:absolute;top:0;left:0;width:1200px;height:114px;background:#fff}
.brand{position:absolute;left:111px;top:10px;width:192px;text-align:center}
.brand-dot{width:56px;height:56px;border-radius:50%;background:var(--ink);margin:0 auto 6px}
.brand-name{font-family:"Roboto",sans-serif;font-weight:500;font-size:24px;color:var(--ink);letter-spacing:1px;white-space:nowrap}
.topbar{position:absolute;left:347px;top:18px;width:742px;font-size:13px;font-weight:700;display:flex;align-items:center}
.welcome{color:var(--green);flex:1}
.topbar .opt{color:#333;margin-left:28px;display:flex;align-items:center;gap:8px}
.flag{width:24px;height:14px;background:linear-gradient(#b22234 0 50%,#fff 50%);position:relative}
.flag:before{content:"";position:absolute;left:0;top:0;width:10px;height:8px;background:#3c3b6e}
.nav{position:absolute;left:347px;top:78px;width:742px;display:flex;justify-content:space-between;font-size:13.5px;font-weight:700;color:#111}
.nav .active{color:var(--green);border-bottom:2px solid var(--green);padding-bottom:5px}

/* hero */
.hero{position:absolute;top:114px;left:0;width:1200px;height:600px;background:radial-gradient(ellipse at 60% 35%,#6a4526 0%,#3a2414 45%,#140b06 100%)}
.hero h1{position:absolute;top:410px;width:100%;text-align:center;color:#fff;font-size:34px;line-height:43px;letter-spacing:.5px}
.dots{position:absolute;left:1140px;top:236px;display:flex;flex-direction:column;gap:11px}
.dots span{width:8px;height:8px;border-radius:50%;background:#fff}
.dots span.on{background:transparent;border:2px solid #fff}

/* products */
.section-title{position:absolute;width:1200px;text-align:center;font-size:34px}
.products{position:absolute;left:111px;top:874px;display:flex;gap:10px}
.card{width:237px;height:334px;border:1px solid var(--line);text-align:center;padding-top:18px}
.card.raised{box-shadow:0 4px 14px rgba(0,0,0,.12);border-color:#eee}
.bottle{width:56px;height:162px;margin:0 auto;border-radius:14px 14px 20px 20px;background:linear-gradient(90deg,#7a4510,#d48a2c 50%,#8a5016)}
.card h3{font-size:14px;font-weight:700;color:#111;margin-top:22px}
.price{font-size:26px;font-weight:500;color:var(--green);margin-top:12px}
.card .row{display:flex;justify-content:space-between;align-items:center;padding:0 38px 0 40px;margin-top:14px}
.stars{color:var(--star);font-size:13px;letter-spacing:1px}
.cart{width:32px;height:30px;border:2px solid var(--green);display:flex;align-items:center;justify-content:center}
.cart.fill{background:var(--green)}
.btn{position:absolute;background:var(--green);color:#fff;font-weight:700;font-size:14px;display:flex;align-items:center;justify-content:center;gap:10px}
.btn-all{left:499px;top:1262px;width:203px;height:48px;border-radius:24px}
.arrow-dot{width:14px;height:14px;border-radius:50%;background:#fff;display:flex;align-items:center;justify-content:center}

/* about */
.about{position:absolute;top:1407px;left:0;width:1200px;height:566px;background:linear-gradient(110deg,#1db596 0%,#109e85 55%,#0a8a74 100%)}
.photo-a{position:absolute;left:111px;top:83px;width:409px;height:289px;background:linear-gradient(135deg,#d8cbb1,#a98f66)}
.photo-b{position:absolute;left:200px;top:261px;width:366px;height:221px;border:8px solid var(--green);background:linear-gradient(135deg,#4a2617,#1f0f0b)}
.about h2{position:absolute;left:659px;top:135px;color:#fff;font-size:32px}
.about p{position:absolute;left:660px;top:188px;width:425px;color:#fff;font-size:14.5px;line-height:25.7px}
.btn-more{left:660px;top:388px;width:155px;height:49px;background:var(--green-2)}
.btn-more .arrow-dot svg path{fill:var(--green-2)}

/* news */
.news{position:absolute;left:111px;top:2161px;display:flex;gap:11px}
.post{width:318px}
.post .pic{height:220px}
.post .body{padding:0 12px}
.post h3{font-size:15px;font-weight:700;color:#111;margin-top:32px}
.post .bar{width:40px;height:3px;background:var(--green);margin:12px 0 14px}
.post p{font-size:14.5px;line-height:24px;color:#666}
.post .meta{border-top:1px solid var(--line);border-bottom:1px solid var(--line);margin-top:16px;height:38px;display:flex;align-items:center;gap:34px;font-size:13.5px;color:#666;padding-left:12px}
.meta span{display:flex;align-items:center;gap:12px}

/* testimonials */
.clients{position:absolute;top:2687px;left:0;width:1200px;height:442px;background:linear-gradient(#1ba58c,#0f8d73 70%,#0c7a63)}
.clients h2{position:absolute;top:70px;width:1200px;text-align:center;color:#fff;font-size:33px}
.quotes{position:absolute;left:110px;top:145px;display:flex;gap:28px}
.quote{width:321px}
.bubble{position:relative;height:146px;background:#fff;padding:28px 20px;font-style:italic;font-size:14.5px;line-height:26px;color:#555}
.bubble:after{content:"";position:absolute;left:26px;bottom:-12px;border:12px solid transparent;border-bottom:0;border-top-color:#fff}
.quote.alt .bubble{background:rgba(255,255,255,.12);color:#fff}
.quote.alt .bubble:after{border-top-color:rgba(255,255,255,.12)}
.qmark{position:absolute;right:20px;bottom:16px;width:28px;height:22px}
.qmark path{fill:var(--green)}
.quote.alt .qmark path{fill:#fff}
.person{display:flex;align-items:center;margin-top:26px;padding-left:22px}
.avatar{width:54px;height:54px;border-radius:50%;background:#d9d9d9;border:3px solid #fff}
.who{margin-left:20px;color:#fff;font-size:14.5px;flex:1}
.who b{display:block;font-weight:700}
.person .stars{margin-right:22px;font-size:15px}

/* footer */
.footer{position:absolute;top:3129px;left:0;width:1200px;height:358px;background:var(--dark);color:#ddd}
.f-logo{position:absolute;left:132px;top:87px;width:186px;height:186px;border-radius:50%;border:6px solid #fff;display:flex;align-items:center;justify-content:center;text-align:center;color:#fff;font-size:21px;font-weight:700;line-height:28px}
.f-col{position:absolute;top:86px}
.f-col h4{color:#fff;font-size:14px;font-weight:700}
.f-col .bar{width:44px;height:3px;background:var(--green);margin:16px 0 20px}
.links li{list-style:none;font-size:13.5px;margin-bottom:16px;display:flex;align-items:center;gap:14px}
.links li:before{content:"»";color:var(--green)}
.contacts li{list-style:none;font-size:13px;display:flex;align-items:center;gap:16px;margin-bottom:18px;line-height:17px}
.ico{width:26px;height:26px;border-radius:50%;background:#444;flex:none;display:flex;align-items:center;justify-content:center}
.sub p{font-size:13.5px;line-height:21px;width:270px}
.email{margin-top:16px;width:256px;height:46px;border-radius:23px;background:#fff;display:flex;align-items:center;overflow:hidden}
.email span{flex:1;padding-left:22px;font-size:13px;color:#666;display:flex;align-items:center;gap:14px}
.email i{width:46px;height:46px;background:var(--green);display:flex;align-items:center;justify-content:center;border-radius:0 23px 23px 0}
.socials{display:flex;gap:10px;margin-top:20px}
.socials span{width:30px;height:30px;border-radius:50%;background:#fff;border:3px solid var(--green)}
.copy{position:absolute;top:3487px;left:0;width:1200px;height:49px;background:var(--green);color:#fff;font-size:14.5px;display:flex;align-items:center;justify-content:center}
</style>
</head>
<body>

<header class="header">
  <div class="brand"><div class="brand-dot"></div><div class="brand-name">TIDE &amp; THISTLE</div></div>
  <div class="topbar">
    <span class="welcome">WELCOME TO TIDE &amp; THISTLE</span>
    <span class="opt"><i class="flag"></i>&nbsp; ENG ⌄</span>
    <span class="opt" style="margin-left:48px">USD ⌄</span>
    <span class="opt" style="margin-left:56px">(0) ITEMS
      <svg width="14" height="12" viewBox="0 0 14 12"><path d="M0 0h3l2 7h7l2-5H4" fill="none" stroke="#333" stroke-width="1.6"/><circle cx="6" cy="10" r="1.3" fill="#333"/><circle cx="11" cy="10" r="1.3" fill="#333"/></svg></span>
  </div>
  <nav class="nav">
    <a class="active">HOME</a><a>ABOUT US</a><a>OUR PRODUCTS</a><a>CATEGORIES</a><a>LATEST BLOG</a><a>REVIEWS</a><a>CONTACT US</a>
  </nav>
</header>

<section class="hero" role="img" aria-label="Friends toasting with champagne glasses in a warmly lit bar">
  <h1 class="serif" style="color:#fff">Celebrate life with family,<br>old &amp; new friends</h1>
  <div class="dots"><span></span><span></span><span class="on"></span><span></span><span></span></div>
</section>

<h2 class="serif section-title" style="top:786px">Featured Products</h2>
<div class="products">
  <div class="card"><div class="bottle" role="img" aria-label="Tide &amp; Thistle rum bottle"></div><h3>PRODUCT TITLE</h3><div class="price">$ 23.00</div><div class="row"><span class="stars">★★★★★</span><span class="cart"><svg width="14" height="12" viewBox="0 0 14 12"><path d="M0 0h3l2 7h7l2-5H4" fill="none" stroke="#00ab8e" stroke-width="1.8"/><circle cx="6" cy="10" r="1.4" fill="#00ab8e"/><circle cx="11" cy="10" r="1.4" fill="#00ab8e"/></svg></span></div></div>
  <div class="card"><div class="bottle" role="img" aria-label="Tide &amp; Thistle rum bottle"></div><h3>PRODUCT TITLE</h3><div class="price">$ 23.00</div><div class="row"><span class="stars">★★★★★</span><span class="cart"><svg width="14" height="12" viewBox="0 0 14 12"><path d="M0 0h3l2 7h7l2-5H4" fill="none" stroke="#00ab8e" stroke-width="1.8"/><circle cx="6" cy="10" r="1.4" fill="#00ab8e"/><circle cx="11" cy="10" r="1.4" fill="#00ab8e"/></svg></span></div></div>
  <div class="card raised"><div class="bottle" role="img" aria-label="Tide &amp; Thistle rum bottle"></div><h3>PRODUCT TITLE</h3><div class="price">$ 23.00</div><div class="row"><span class="stars">★★★★★</span><span class="cart fill"><svg width="14" height="12" viewBox="0 0 14 12"><path d="M0 0h3l2 7h7l2-5H4" fill="none" stroke="#fff" stroke-width="1.8"/><circle cx="6" cy="10" r="1.4" fill="#fff"/><circle cx="11" cy="10" r="1.4" fill="#fff"/></svg></span></div></div>
  <div class="card"><div class="bottle" role="img" aria-label="Tide &amp; Thistle rum bottle"></div><h3>PRODUCT TITLE</h3><div class="price">$ 23.00</div><div class="row"><span class="stars">★★★★★</span><span class="cart"><svg width="14" height="12" viewBox="0 0 14 12"><path d="M0 0h3l2 7h7l2-5H4" fill="none" stroke="#00ab8e" stroke-width="1.8"/><circle cx="6" cy="10" r="1.4" fill="#00ab8e"/><circle cx="11" cy="10" r="1.4" fill="#00ab8e"/></svg></span></div></div>
</div>
<a class="btn btn-all">VIEW ALL PRODUCTS <span class="arrow-dot"><svg width="8" height="8" viewBox="0 0 8 8"><path d="M2 1l4 3-4 3z" fill="#00ab8e"/></svg></span></a>

<section class="about">
  <div class="photo-a" role="img" aria-label="Friends cheering with beer bottles in a bright living room"></div>
  <div class="photo-b" role="img" aria-label="Friends raising cocktails at a night party"></div>
  <h2 class="serif" style="color:#fff">About Us</h2>
  <p>Tide &amp; Thistle fulfillment services operate through a national network of licensed retailers, shipping carriers, and customer service professionals to guarantee the best fulfillment and logistics practices. Tide &amp; Thistle fulfillment services operate through a national network of licensed retailers, shipping carriers, and customer service professionals to guarantee the best fulfillment and logistics practices.</p>
  <a class="btn btn-more">LEARN MORE <span class="arrow-dot"><svg width="8" height="8" viewBox="0 0 8 8"><path d="M2 1l4 3-4 3z"/></svg></span></a>
</section>

<h2 class="serif section-title" style="top:2075px">Latest News</h2>
<div class="news">
  <article class="post"><div class="pic" role="img" aria-label="Friends clinking glasses at a festive bar" style="background:linear-gradient(135deg,#6b4a2a,#24150c)"></div><div class="body"><h3>PERSPICIATIS UNDE</h3><div class="bar"></div><p>Lorem ipsum dolor sit amet, consectetur adipiscing elit, sed do eiusmod tempor incididunt ut labore et dolor</p></div><div class="meta"><span><svg width="13" height="13" viewBox="0 0 13 13"><rect x="1" y="2" width="11" height="10" fill="#00ab8e"/><rect x="2.5" y="5" width="8" height="5.5" fill="#fff"/></svg>Sep 01 , 2021</span><span><svg width="16" height="12" viewBox="0 0 16 12"><ellipse cx="6" cy="5" rx="6" ry="4.5" fill="#00ab8e"/><ellipse cx="11" cy="8" rx="5" ry="3.5" fill="none" stroke="#00ab8e" stroke-width="1.4"/></svg>No Comments</span></div></article>
  <article class="post"><div class="pic" role="img" aria-label="Group celebrating with drinks in a crowded bar" style="background:linear-gradient(135deg,#3c3a40,#15121a)"></div><div class="body"><h3>PERSPICIATIS UNDE</h3><div class="bar"></div><p>Lorem ipsum dolor sit amet, consectetur adipiscing elit, sed do eiusmod tempor incididunt ut labore et dolor</p></div><div class="meta"><span><svg width="13" height="13" viewBox="0 0 13 13"><rect x="1" y="2" width="11" height="10" fill="#00ab8e"/><rect x="2.5" y="5" width="8" height="5.5" fill="#fff"/></svg>Sep 01 , 2021</span><span><svg width="16" height="12" viewBox="0 0 16 12"><ellipse cx="6" cy="5" rx="6" ry="4.5" fill="#00ab8e"/><ellipse cx="11" cy="8" rx="5" ry="3.5" fill="none" stroke="#00ab8e" stroke-width="1.4"/></svg>No Comments</span></div></article>
  <article class="post"><div class="pic" role="img" aria-label="Holiday dinner toast with red wine" style="background:linear-gradient(135deg,#5a3a22,#a8744a)"></div><div class="body"><h3>PERSPICIATIS UNDE</h3><div class="bar"></div><p>Lorem ipsum dolor sit amet, consectetur adipiscing elit, sed do eiusmod tempor incididunt ut labore et dolor</p></div><div class="meta"><span><svg width="13" height="13" viewBox="0 0 13 13"><rect x="1" y="2" width="11" height="10" fill="#00ab8e"/><rect x="2.5" y="5" width="8" height="5.5" fill="#fff"/></svg>Sep 01 , 2021</span><span><svg width="16" height="12" viewBox="0 0 16 12"><ellipse cx="6" cy="5" rx="6" ry="4.5" fill="#00ab8e"/><ellipse cx="11" cy="8" rx="5" ry="3.5" fill="none" stroke="#00ab8e" stroke-width="1.4"/></svg>No Comments</span></div></article>
</div>

<section class="clients">
  <h2 class="serif" style="color:#fff">What Our Clients Say</h2>
  <div class="quotes">
    <div class="quote"><div class="bubble">Sed ut perspiciatis unde omnis iste natus error sit voluptatem accusantiudoloremque laudantium, totam rem aperiam<svg class="qmark" viewBox="0 0 28 22"><path d="M0 0h12v11q0 8-7 11l-2-3q4-2 4-6H0zM16 0h12v11q0 8-7 11l-2-3q4-2 4-6h-7z"/></svg></div><div class="person"><div class="avatar" role="img" aria-label="Client portrait"></div><div class="who"><b>NORA VALE</b>Businessman</div><span class="stars">★★★★★</span></div></div>
    <div class="quote alt"><div class="bubble">Sed ut perspiciatis unde omnis iste natus error sit voluptatem accusantiudoloremque laudantium, totam rem aperiam<svg class="qmark" viewBox="0 0 28 22"><path d="M0 0h12v11q0 8-7 11l-2-3q4-2 4-6H0zM16 0h12v11q0 8-7 11l-2-3q4-2 4-6h-7z"/></svg></div><div class="person"><div class="avatar" role="img" aria-label="Client portrait"></div><div class="who"><b>NORA VALE</b>Businessman</div><span class="stars">★★★★★</span></div></div>
    <div class="quote"><div class="bubble">Sed ut perspiciatis unde omnis iste natus error sit voluptatem accusantiudoloremque laudantium, totam rem aperiam<svg class="qmark" viewBox="0 0 28 22"><path d="M0 0h12v11q0 8-7 11l-2-3q4-2 4-6H0zM16 0h12v11q0 8-7 11l-2-3q4-2 4-6h-7z"/></svg></div><div class="person"><div class="avatar" role="img" aria-label="Client portrait"></div><div class="who"><b>NORA VALE</b>Businessman</div><span class="stars">★★★★★</span></div></div>
  </div>
</section>

<footer class="footer">
  <div class="f-logo">TIDE &amp;<br>THISTLE</div>
  <div class="f-col" style="left:395px">
    <h4>QUICK LINKS</h4><div class="bar"></div>
    <ul class="links"><li>Home</li><li>About Us</li><li>Our Products</li><li>Reviews</li><li>Contact Us</li></ul>
  </div>
  <div class="f-col" style="left:578px">
    <h4>CONTACT US</h4><div class="bar"></div>
    <ul class="contacts">
      <li><span class="ico"><svg width="12" height="12" viewBox="0 0 12 12"><path d="M2 1l2 0 1 3-1.5 1a7 7 0 0 0 3.5 3.5L8 7l3 1v2l-1 1C5 11 1 7 1 2z" fill="#ddd"/></svg></span>1 800 555 0148</li>
      <li><span class="ico"><svg width="12" height="9" viewBox="0 0 12 9"><rect width="12" height="9" fill="#ddd"/><path d="M0 0l6 5 6-5" fill="none" stroke="#444"/></svg></span>info@tideandthistle.co.nz</li>
      <li><span class="ico"><svg width="10" height="13" viewBox="0 0 10 13"><path d="M5 13S0 7 0 5a5 5 0 0 1 10 0c0 2-5 8-5 8z" fill="#ddd"/><circle cx="5" cy="5" r="2" fill="#444"/></svg></span>PO Box 5180 Harborview<br>United States</li>
      <li><span class="ico"><svg width="12" height="10" viewBox="0 0 12 10"><path d="M0 1l4-1 4 1 4-1v9l-4 1-4-1-4 1z" fill="#ddd"/></svg></span><u>View Other Location</u></li>
    </ul>
  </div>
  <div class="f-col sub" style="left:824px">
    <h4>SUBSCRIBE NOW</h4><div class="bar"></div>
    <p>Sed ut perspiciatis unde omnis iste natus error sit voluptatem accusantium</p>
    <div class="email"><span><svg width="12" height="9" viewBox="0 0 12 9"><rect width="12" height="9" fill="#555"/><path d="M0 0l6 5 6-5" fill="none" stroke="#fff"/></svg>Email Address</span><i><svg width="14" height="14" viewBox="0 0 14 14"><path d="M0 6L14 0 9 14 7 8z" fill="#fff"/></svg></i></div>
    <div class="socials"><span></span><span></span><span></span><span></span></div>
  </div>
</footer>
<div class="copy">© 2021 Tide &amp; Thistle . All Rights Reserved</div>

</body>
</html>
```